Business Card Design

Business Card for professional consulting firm working with large financial institutions.

Target Market(s)

Executive buyers

Industry/Entity Type

Banking

Contact Information for Business Card

Mild creativity wanted. Not boring, but do elaborate artwork.

Font styles to use
Serif
Sans Serif

Colors

Designer to choose colors to be used in the design.

Requirements
Must have
• Standard business card features - company name, individual name, telephone, website, email, locations.
Nice to have
• Two colors
Should not have
• too many colors, fancy printing, cartoons.

```html
<!DOCTYPE html>
<html lang="en">
<head>
<meta charset="utf-8">
<title>k7advisory business cards</title>
<link href="https://fonts.googleapis.com/css2?family=Tinos:wght@400;700&display=swap" rel="stylesheet">
<style>
  :root {
    --stage: #2b2520;
    --card-black: #0b0b0b;
    --card-black-soft: #1c1c1c;
    --card-white: #f3f3f3;
    --edge-grey: #d5d5d5;
    --text-light: #d8d8d8;
    --text-muted: #a9a9a9;
    --text-dark: #161616;
    --rule: #8a8a8a;
  }
  html, body {
    margin: 0;
    padding: 0;
    width: 1200px;
    height: 886px;
    overflow: hidden;
    background: var(--stage);
    font-family: "Tinos", "Times New Roman", serif;
  }
  .canvas {
    position: relative;
    width: 1200px;
    height: 886px;
  }
  .card {
    position: absolute;
    width: 600px;
    height: 343px;
    border-radius: 22px;
    overflow: hidden;
    box-shadow: 0 14px 30px rgba(0,0,0,.55);
  }
  .card-back {
    left: 70px;
    top: 80px;
    background: linear-gradient(100deg, var(--card-black) 0%, var(--card-black-soft) 45%, var(--card-black) 100%);
  }
  .card-front {
    left: 530px;
    top: 450px;
    background: var(--card-black);
  }
  .card-front svg {
    position: absolute;
    inset: 0;
  }
  .wordmark {
    position: absolute;
    font-weight: 400;
    letter-spacing: 0.5px;
    white-space: nowrap;
  }
  .card-back .wordmark {
    left: 0;
    right: 0;
    top: 142px;
    text-align: center;
    font-size: 46px;
    color: var(--text-light);
  }
  .card-front .wordmark {
    left: 0;
    right: 0;
    top: 76px;
    text-align: center;
    font-size: 48px;
    color: var(--text-dark);
  }
  .details {
    position: absolute;
    left: 28px;
    right: 24px;
    bottom: 24px;
    display: flex;
    align-items: flex-end;
    color: var(--text-muted);
    font-size: 15px;
    line-height: 1.3;
  }
  .person { width: 190px; }
  .person-name {
    font-weight: 700;
    font-size: 22px;
    color: var(--text-light);
  }
  .person-title { font-size: 17px; }
  .rule {
    width: 1px;
    height: 60px;
    background: var(--rule);
    margin: 0 18px;
  }
  .address { width: 210px; }
  .contact { flex: 1; }
</style>
</head>
<body>
<main class="canvas">
  <section class="card card-back" aria-label="Card back">
    <div class="wordmark">k7advisory</div>
  </section>

  <section class="card card-front" aria-label="Card front">
    <svg width="600" height="343" viewBox="0 0 600 343" aria-hidden="true">
      <path d="M0 0 H600 V222 C470 250 200 220 0 128 Z" fill="var(--edge-grey)"/>
      <path d="M0 0 H600 V212 C470 240 200 210 0 120 Z" fill="var(--card-white)"/>
    </svg>
    <div class="wordmark">k7advisory</div>
    <div class="details">
      <div class="person">
        <div class="person-name">Daniel Reyes</div>
        <div class="person-title">Managing Director</div>
      </div>
      <div class="rule"></div>
      <div class="address">
        k7advisory<br>
        4120 Cedar Ridge Road<br>
        Juneau, Alaska 99801
      </div>
      <div class="rule"></div>
      <div class="contact">
        555 210 4817<br>
        info@k7advisory.com<br>
        www.k7advisory.com
      </div>
    </div>
  </section>
</main>
</body>
</html>
```